Detail Shop Business card design

i need a business card design for my new detailing company called 'Brisk's Polish Works'. i want an all black and white design . simple, direct and to the point. i want the designer to choose a fitting font to match the logothe front should have logo, address, phone and email and the back side should have a slogan and text indicating that we offer services on anything including cars, trucks, motorcycles and RVs. slogan will read "we take pride in your ride"
maybe also very small on the back side the IG icon with Brisks_Polish_Works

phone 208.417.6352
address 3847 E Larkin Ave
Spokane WA 99214
email: BrisksPolish@mailvexo.com

Target Market(s)

all ages , auto enthusiasts

Industry/Entity Type

Automotive

Contact Information for Business Card

the front should have logo, address, phone and email and the back side should have a slogan and text indicating that we offer services on anything including cars, trucks, motorcycles and RVs. slogan will read "we take pride in your ride"

phone 208.417.6352
address 3847 E Larkin Ave
Spokane WA 99214

Colors
000000
ffffff

Requirements
Must have
• bold font and very simple design with good spacing
Nice to have
• anything creative from the designer indicating we service any types of vehicles
Should not have
• any colors ,

```html
<!DOCTYPE html>
<html lang="en">
<head>
<meta charset="utf-8">
<title>Brisk's Polish Works – Business Card</title>
<link href="https://fonts.googleapis.com/css2?family=Roboto:wght@400;700&family=Roboto+Condensed:wght@400;700&display=swap" rel="stylesheet">
<style>
  :root{
    --ink:#000000;
    --paper:#ffffff;
    --stage:#2e2e2e;
    --muted:#555555;
  }
  *{margin:0;padding:0;box-sizing:border-box}
  html,body{width:1200px;height:960px;overflow:hidden;background:var(--stage)}
  .canvas{position:relative;width:1200px;height:960px}
  .card{position:absolute;width:600px;height:342px;overflow:hidden}
  .card--front{left:322px;top:110px;background:var(--paper)}
  .card--back{left:320px;top:493px;background:var(--ink)}

  .brand{position:absolute;left:40px;top:58px;width:190px;display:flex;align-items:center;gap:10px;
    font-family:"Roboto Condensed",sans-serif;font-weight:700;font-size:26px;line-height:1.05;color:var(--ink)}
  .brand__dot{flex:0 0 auto;width:22px;height:22px;border-radius:50%;background:var(--ink)}

  .name-ribbon{position:absolute;right:0;top:86px;width:214px;height:60px}
  .name-ribbon svg{position:absolute;inset:0}
  .name-ribbon__text{position:absolute;right:34px;top:8px;text-align:right;color:var(--paper);
    font-family:"Roboto Condensed",sans-serif}
  .name-ribbon__name{font-weight:700;font-size:21px;line-height:24px}
  .name-ribbon__role{font-size:14px;line-height:18px}

  .contacts{position:absolute;right:34px;top:201px;list-style:none;font-family:"Roboto",sans-serif;
    font-size:14px;color:var(--muted);text-align:right}
  .contacts li{height:19.3px;line-height:19.3px;display:flex;justify-content:flex-end;align-items:center;gap:10px}
  .contacts svg{width:12px;height:12px;fill:var(--ink)}

  .address-band{position:absolute;left:0;right:0;top:294px;height:28px;background:var(--ink);
    display:flex;justify-content:flex-end;align-items:center;gap:12px;padding-right:34px;
    font-family:"Roboto",sans-serif;font-size:14px;color:var(--paper)}
  .address-band svg{width:12px;height:15px;fill:var(--paper)}

  .vehicle-art{position:absolute;left:113px;top:92px;width:382px;height:135px;
    background:linear-gradient(180deg,#d9d9d9 0%,#9a9a9a 70%,#ffffff 100%);border-radius:40px 40px 6px 6px}

  .slogan{position:absolute;left:0;right:0;top:271px;text-align:center;font-family:"Roboto",sans-serif;
    font-weight:700;font-size:17px;color:var(--paper);letter-spacing:.3px}
  .slogan span{display:inline-block;padding:0 8px 3px;border-bottom:2px solid var(--paper)}
  .services{position:absolute;left:0;right:0;top:303px;text-align:center;font-family:"Roboto",sans-serif;
    font-weight:700;font-size:11px;color:var(--paper)}
</style>
</head>
<body>
<div class="canvas">

  <section class="card card--front">
    <div class="brand"><span class="brand__dot"></span><span>Brisk's Polish Works</span></div>

    <div class="name-ribbon">
      <svg viewBox="0 0 214 60" width="214" height="60"><polygon points="0,0 214,0 214,60 30,60 16,30" fill="#000"/></svg>
      <div class="name-ribbon__text">
        <div class="name-ribbon__name">DEAN MARLOW</div>
        <div class="name-ribbon__role">OWNER</div>
      </div>
    </div>

    <ul class="contacts">
      <li>208.417.6352 <svg viewBox="0 0 24 24"><path d="M6.6 10.8a15 15 0 0 0 6.6 6.6l2.2-2.2c.3-.3.7-.4 1-.2 1.1.4 2.3.6 3.6.6.6 0 1 .4 1 1V20c0 .6-.4 1-1 1A17 17 0 0 1 3 4c0-.6.4-1 1-1h3.5c.6 0 1 .4 1 1 0 1.3.2 2.5.6 3.6.1.3 0 .7-.2 1z"/></svg></li>
      <li>836 274 5108 <svg viewBox="0 0 24 24"><path d="M7 1h10a2 2 0 0 1 2 2v18a2 2 0 0 1-2 2H7a2 2 0 0 1-2-2V3a2 2 0 0 1 2-2zm0 3v14h10V4z"/></svg></li>
      <li>BrisksPolish@mailvexo.com <svg viewBox="0 0 24 24"><path d="M2 5h20v14H2zm2 2v.5l8 5 8-5V7l-8 5z"/></svg></li>
      <li>www.briskspolish.com <svg viewBox="0 0 24 24"><circle cx="12" cy="12" r="10"/></svg></li>
    </ul>

    <div class="address-band">3847 E Larkin Ave, Spokane WA 99214
      <svg viewBox="0 0 24 30"><path d="M12 0a10 10 0 0 0-10 10c0 7.5 10 20 10 20s10-12.5 10-20A10 10 0 0 0 12 0zm0 14a4 4 0 1 1 0-8 4 4 0 0 1 0 8z"/></svg>
    </div>
  </section>

  <section class="card card--back">
    <div class="vehicle-art" role="img" aria-label="White illustration of a classic hot rod car"></div>
    <div class="slogan"><span>WE TAKE PRIDE IN YOUR RIDE</span></div>
    <div class="services">CARS●TRUCKS●MOTORCYCLES●RVS AND BOATS</div>
  </section>

</div>
</body>
</html>
```